Print materials for 3-star hotel

We are changing up our print materials (notepads, letterheads, key card jackets, small flyer for the room rates) We are a 3 star business hotel in the Philippines and have mainly used grey tones and clean, simple lines. See attached photos for logo and hotel interior photos.

Target Market(s)

Business

Contact Information for Business Card

Corvale Terrace Hotel
Lindwell Banca Avenue corner Tolenta St Cebu City 6000 Philippines
Tel: +63 32 481 7302
Mobile: +63 917 648 2095
www.corvaleterracehotel.example

Font styles to use
Serif
Sans Serif

Requirements
Must have
• Simple
• Readable font and font size
Nice to have
• Neutral colors, grey and taupes
Should not have
• No purples and bright blues

```html
<!DOCTYPE html>
<html lang="en">
<head>
<meta charset="utf-8">
<title>Corvale Terrace Hotel – Business Card</title>
<link href="https://fonts.googleapis.com/css2?family=Roboto:wght@400;500&display=swap" rel="stylesheet">
<style>
  :root {
    --backdrop: #2a2a2a;
    --card: #1f1f1f;
    --ink: #f2f2f2;
    --ink-soft: #dcdcdc;
    --rule: #6a6a6a;
  }
  * { margin: 0; padding: 0; box-sizing: border-box; }
  html, body { width: 1200px; height: 960px; overflow: hidden; }
  body {
    background: var(--backdrop);
    position: relative;
    font-family: "Roboto", Arial, sans-serif;
    color: var(--ink);
  }
  .card {
    position: absolute;
    background: var(--card);
    box-shadow: 0 2px 6px rgba(0,0,0,.45);
  }
  .card--front { left: 316px; top: 113px; width: 598px; height: 343px; }
  .card--back  { left: 316px; top: 474px; width: 596px; height: 340px; }

  .brand {
    position: absolute;
    left: 40px; top: 178px;
    width: 250px;
    text-align: center;
    font-weight: 400;
    font-size: 17px;
    letter-spacing: 3px;
    line-height: 22px;
    color: var(--ink);
    text-transform: uppercase;
  }
  .divider {
    position: absolute;
    left: 316px; top: 67px;
    width: 1px; height: 225px;
    background: var(--rule);
  }
  .details { position: absolute; left: 345px; top: 72px; }
  .person-name { font-size: 21px; font-weight: 500; line-height: 26px; }
  .person-title { font-size: 15px; font-weight: 500; line-height: 18px; }
  .address { margin-top: 12px; font-size: 15px; line-height: 18px; color: var(--ink-soft); }
  .contacts { list-style: none; margin-top: 11px; }
  .contacts li {
    display: flex; align-items: center;
    font-size: 14.5px; line-height: 19px; color: var(--ink-soft);
  }
  .contacts svg { width: 14px; height: 14px; margin-right: 9px; fill: var(--ink); flex: none; }

  .back-brand {
    position: absolute; left: 0; right: 0; top: 150px;
    text-align: center;
    font-size: 22px; font-weight: 400;
    letter-spacing: 5px; text-transform: uppercase;
  }
  .back-web {
    position: absolute; left: 0; right: 0; top: 283px;
    text-align: center;
    font-size: 15px; letter-spacing: 4px; color: var(--ink-soft);
  }
</style>
</head>
<body>
  <section class="card card--front">
    <div class="brand">Corvale Terrace<br>Hotel</div>
    <div class="divider"></div>
    <div class="details">
      <div class="person-name">MARCO ALDANA</div>
      <div class="person-title">CEO/FOUNDER</div>
      <div class="address">12 Lindwell Banca Avenue<br>Cebu City 6000 Philippines</div>
      <ul class="contacts">
        <li><svg viewBox="0 0 16 16"><path d="M3 1l3 3-2 2c1 2 3 4 5 5l2-2 3 3-2 3C7 15 1 9 0 4z"/></svg>+63 32 481 7302</li>
        <li><svg viewBox="0 0 16 16"><path d="M4 0h8v16H4zM5.5 2v11h5V2z"/></svg>+63 917 648 2095</li>
        <li><svg viewBox="0 0 16 16"><path d="M4 1h8v4H4zM1 6h14v6H1zM4 10h8v5H4z"/></svg>+63 32 481 7310</li>
        <li><svg viewBox="0 0 16 16"><path d="M1 3h14v10H1zM2 4l6 5 6-5v1L8 10 2 5z" fill-rule="evenodd"/></svg>stay@corvaleterrace.example</li>
        <li><svg viewBox="0 0 16 16"><circle cx="8" cy="8" r="7"/></svg>www.corvaleterracehotel.example</li>
      </ul>
    </div>
  </section>

  <section class="card card--back">
    <div class="back-brand">Corvale Terrace Hotel</div>
    <div class="back-web">www.corvaleterracehotel.example</div>
  </section>
</body>
</html>
```